ONE PAGE WEB DESIGN NEEDED for Finance Company

We need a web design (ONE PAGE DESIGN ONLY) for a new finance website called Tidewell Lending. Tidewell Lending helps customers get the right loan, whether its a home loan, investment loan, business loan etc.

You are required to come up with just the homepage design. Professionalism and quality is the key factors in the successful design.

Here are a few design questions to help you out:

-
What information should be used on the page?
Ive provided a document which outlines all the information needed to put on homepage (attached to the brief - called tidewell_page_info). Also see the Must Have section below on this brief.

-
What links should appear in the navigation/footer?:
The navigation should provide links to the following pages (NOTE: services link has subcategories):
1 Homepage
2 Services
- Home loans
- Investment loans
- Refinancing loans
- Business loans
3 About Us
4 FAQ
5 Contact Us

-
What colors should be used in the design?
Our company colors - Cyan: #2EADE3, Blue: #004B70, White. Feel free to submit designs with slight variations if you feel it improves the design.

-
What should the layout of the page be?
This is up to you to come up with - we are open to different layouts for the page design (as long as they capture the information effectively and making it easy to understand).

Target Market(s)

Potential Home owners, Families and Business Owners

Industry/Entity Type

Business

Requirements
Must have
• - Must contain our logo (attached as PNG and Illustrator file)
- Winning designer must supply a Photoshop file (PSD) that will allow us.
Nice to have
• - Should include photos/images of families, professional groups, tradespeople etc (you can use stock photos from PixaVault and I will purchase them once you are selected as the winning design)
- Link to a loan calculator somewhere on front page with a button 'Find out how much you could borrow' (or maybe even try adding a loan calculator to the homepage if you think this would look good)
- Page should have a main headline "Finding the right loan for you" or "Tidewell Lending finds the right loan for our customers."
- Must include Accreditation logos somewhere on the homepage (will try and supply these soon)
Should not have
• - Poor quality designs will not be considered
- Do not use clipart

```html
<!DOCTYPE html>
<html lang="en">
<head>
<meta charset="utf-8">
<title>Tidewell Lending — Finding the Right Loan for You</title>
<link rel="stylesheet" href="https://fonts.googleapis.com/css2?family=PT+Sans:wght@400;700&family=Arimo:wght@400;700&display=swap">
<style>
:root{
  --cyan:#2eade3;
  --blue:#004b70;
  --blue-mid:#0a5a82;
  --white:#fff;
  --ink:#3a3a3a;
  --grey-text:#555;
  --line-grey:#d7d7d7;
  --card-top:#f4f4f4;
  --card-bottom:#dcdcdc;
  --social:#8c8c8c;
}
*{box-sizing:border-box;margin:0;padding:0}
html,body{width:1021px;height:1200px;overflow:hidden;background:var(--white)}
body{position:relative;font-family:"PT Sans",sans-serif;color:var(--ink)}
.abs{position:absolute}

/* header */
.brand{left:110px;top:30px;display:flex;align-items:center;gap:8px}
.brand-dot{width:26px;height:26px;border-radius:50%;background:var(--cyan)}
.brand-name{font-size:24px;font-weight:700;color:var(--blue);letter-spacing:-.3px}
.social{left:691px;top:17px;display:flex;gap:5px}
.social span{width:23px;height:23px;border-radius:50%;background:var(--social)}
.nav{left:527px;top:66px;width:377px;height:29px;border-top:3px solid #e4e4e4;border-bottom:3px solid #e4e4e4;display:flex;justify-content:space-between;align-items:center;padding:0 7px;font-size:12.5px;color:#333}
.nav a{color:inherit;text-decoration:none}
.nav .current{color:var(--blue);font-weight:700}

/* hero */
.hero{left:110px;top:113px;width:591px;height:254px;border-radius:4px;overflow:hidden;
  background:linear-gradient(180deg,#b8d4ea 0%,#d8d2be 30%,#a9a08a 55%,#5f8a3c 80%,#3f6b26 100%)}
.hero-card{left:397px;top:37px;width:194px;height:160px;background:rgba(255,255,255,.72);padding:8px 8px}
.hero-card h1{font-size:21px;line-height:20px;font-weight:700;color:#111}
.hero-card p{margin-top:8px;font-size:10px;line-height:15px;text-align:justify;color:#222}
.hero-btn{left:405px;top:166px;width:163px;height:30px;background:linear-gradient(#0f628d,var(--blue));color:#fff;font-size:12px;font-weight:700;display:flex;align-items:center;justify-content:center;letter-spacing:.3px;border-radius:2px}
.dots{display:flex;gap:4px}
.dots i{width:9px;height:9px;border-radius:50%;background:#fff;display:block}
.dots i.on{background:var(--blue)}
.hero .dots{position:absolute;left:520px;top:233px}

/* calculator */
.calc{left:720px;top:113px;width:184px;height:254px;background:var(--blue);border-radius:4px;padding:11px 9px}
.calc h2{font-size:13.5px;color:#fff;text-align:center;padding-bottom:5px;border-bottom:2px solid #fff;margin:0 0 16px}
.calc .field{height:21px;background:#fff;border:1px solid #c9c9c9;margin-bottom:14px;font-size:9.5px;color:#999;padding:4px 6px}
.calc .btn{margin:23px auto 0;width:122px;height:24px;background:linear-gradient(#fff,#d4d4d4);color:var(--blue);font-size:11.5px;font-weight:700;display:flex;align-items:center;justify-content:center}
.calc .result{margin-top:10px;text-align:center;color:#fff;font-size:10px;font-weight:700}
.calc .result b{font-size:12px;font-weight:400;margin-left:4px}

/* section headings */
.tab-head{height:22px;border-bottom:2px solid var(--cyan)}
.tab-head span{display:inline-block;height:22px;background:var(--cyan);color:#fff;font-size:11.5px;font-weight:700;padding:4px 9px 0;text-transform:uppercase}

/* services */
.card{top:455px;width:184px;height:162px;background:linear-gradient(var(--card-top),var(--card-bottom));border:1px solid #cfcfcf;padding:38px 18px 0}
.card-icon{position:absolute;left:62px;top:-34px;width:58px;height:58px;border-radius:50%;background:#fff;box-shadow:0 1px 2px rgba(0,0,0,.15);display:flex;align-items:center;justify-content:center}
.card-icon div{width:50px;height:50px;border-radius:50%;background:var(--blue);display:flex;align-items:center;justify-content:center}
.card h3{font-size:12px;color:var(--blue);text-align:center;padding-bottom:2px;border-bottom:2px solid var(--blue);margin-bottom:8px}
.card ul{list-style:none;font-size:10px;line-height:12px;color:#333}
.card li{position:relative;padding-left:15px;margin-bottom:8px}
.card li::before{content:"";position:absolute;left:3px;top:3px;width:5px;height:5px;border-radius:50%;background:var(--cyan)}
.card .go{position:absolute;right:20px;bottom:12px}

/* about */
.about{left:110px;top:645px;width:591px}
.about-body{margin-top:14px;font-family:"Arimo",sans-serif;font-size:9.6px;line-height:15.2px;color:var(--grey-text)}
.about-body p{margin-bottom:15px}
.about-body b{color:var(--blue);font-size:11px}

/* testimonial */
.testi{left:720px;top:645px;width:184px}
.quote{position:relative;margin-top:23px;background:var(--blue);color:#fff;padding:20px 17px 10px 18px;font-size:10px;line-height:15.3px;height:128px}
.quote cite{display:block;margin-top:7px;font-style:normal}
.quote::after{content:"";position:absolute;left:92px;bottom:-24px;border-top:24px solid var(--blue);border-left:34px solid transparent}
.testi .dots{position:absolute;left:152px;top:198px}
.testi .dots i{width:7px;height:7px;background:#9aa3a8}
.testi .dots i.on{background:var(--blue)}

.rule{left:110px;top:869px;width:794px;height:1px;background:#e2e2e2}

/* clients */
.clients{left:110px;top:893px;width:794px}
.client-row{margin-top:14px;display:flex;border:1px solid var(--line-grey);height:61px}
.client-row div{flex:1;border-right:1px solid var(--line-grey);display:flex;align-items:center;justify-content:center;font-size:16px;font-weight:700;color:#7c7c7c}
.client-row div:last-child{border-right:0}

/* footer */
.footer{left:110px;top:1007px;width:794px;height:184px;background:var(--blue);color:#fff;padding:15px 13px 0}
.footer h4{font-size:11px;text-transform:uppercase;margin-bottom:13px}
.fcol{position:absolute;top:15px;font-size:10px}
.fcol ul{list-style:none}
.fcol li{margin-bottom:8px}
.contact-line{display:flex;gap:6px;margin-bottom:10px;line-height:15px}
.contact-line svg{flex:none;margin-top:2px}
.news-input{width:167px;height:21px;background:#fff;border:1px solid #aaa;font-size:9.5px;color:#999;padding:4px 6px;margin-top:10px}
.news-btn{margin-top:10px;width:72px;height:20px;background:linear-gradient(#fff,#d4d4d4);color:var(--blue);font-size:10.5px;display:flex;align-items:center;justify-content:center}
.footer-base{position:absolute;left:13px;right:13px;top:140px;border-top:1px solid #6f99b0;padding-top:12px;display:flex;justify-content:space-between;font-family:"Arimo",sans-serif;font-size:9px}
</style>
</head>
<body>

<header>
  <div class="abs brand"><span class="brand-dot"></span><span class="brand-name">tidewell lending</span></div>
  <div class="abs social" aria-label="Social links"><span></span><span></span><span></span><span></span><span></span><span></span><span></span></div>
  <nav class="abs nav">
    <a class="current" href="#">HOME</a><a href="#">SERVICES</a><a href="#">ABOUT US</a><a href="#">FAQ</a><a href="#">CONTACT US</a>
  </nav>
</header>

<section class="abs hero" role="img" aria-label="Photo of a young family holding their baby in front of their new home">
  <div class="abs hero-card">
    <h1>Finding the Right Loan for you</h1>
    <p>Lorem ipsum dolor sit amet, consectetur adipisicing elit, sed do eiusmod tempor incididunt ut labore et dolore magna aliqua.</p>
  </div>
  <div class="abs hero-btn">Contact Us</div>
  <div class="dots"><i class="on"></i><i></i><i></i><i></i></div>
</section>

<aside class="abs calc">
  <h2>LOAN CALCULATOR</h2>
  <div class="field">Amount</div>
  <div class="field">Down Payment</div>
  <div class="field">Years</div>
  <div class="field">Rate</div>
  <div class="btn">Calculate</div>
  <div class="result">Monthly Payment: <b>$00.00</b></div>
</aside>

<div class="abs tab-head" style="left:110px;top:390px;width:811px"><span>We offer a unique approach to help you find the right</span></div>

<article class="abs card" style="left:110px">
  <div class="card-icon"><div><svg width="28" height="28" viewBox="0 0 28 28"><path d="M14 3 2 14h4v11h6v-7h4v7h6V14h4z" fill="#fff"/></svg></div></div>
  <h3>HOME LOAN</h3>
  <ul><li>Home Buyers</li><li>First Home Buyers</li><li>Over 20 Lenders</li></ul>
  <svg class="go" width="20" height="20" viewBox="0 0 20 20"><circle cx="10" cy="10" r="10" fill="#004b70"/><path d="M8 5l5 5-5 5" stroke="#fff" stroke-width="2.5" fill="none"/></svg>
</article>

<article class="abs card" style="left:313px">
  <div class="card-icon"><div><svg width="30" height="24" viewBox="0 0 30 24"><path d="M1 22V12l4-4v4l4-6v6l3-3V3l3 4v5l3-4 3 4V5l4 5v12z" fill="#fff"/></svg></div></div>
  <h3>INVESTMENT LOAN</h3>
  <ul><li>Property Investment Loans</li><li>Interest only Loans</li></ul>
  <svg class="go" width="20" height="20" viewBox="0 0 20 20"><circle cx="10" cy="10" r="10" fill="#004b70"/><path d="M8 5l5 5-5 5" stroke="#fff" stroke-width="2.5" fill="none"/></svg>
</article>

<article class="abs card" style="left:518px">
  <div class="card-icon"><div><svg width="30" height="30" viewBox="0 0 30 30"><path d="M6 13a9 9 0 0 1 16-5" stroke="#fff" stroke-width="3.5" fill="none"/><path d="M24 3v8h-8z" fill="#fff"/><path d="M24 17a9 9 0 0 1-16 5" stroke="#fff" stroke-width="3.5" fill="none"/><path d="M6 27v-8h8z" fill="#fff"/></svg></div></div>
  <h3>REFINANCING</h3>
  <ul><li>Refinancing for the best rate</li><li>Upsizing or downsizing</li><li>Change from a variable to a fixed rate</li></ul>
  <svg class="go" width="20" height="20" viewBox="0 0 20 20"><circle cx="10" cy="10" r="10" fill="#004b70"/><path d="M8 5l5 5-5 5" stroke="#fff" stroke-width="2.5" fill="none"/></svg>
</article>

<article class="abs card" style="left:720px">
  <div class="card-icon"><div><svg width="30" height="30" viewBox="0 0 30 30"><circle cx="15" cy="15" r="10" fill="none" stroke="#fff" stroke-width="5" stroke-dasharray="4 3"/><circle cx="15" cy="15" r="8" fill="#fff"/><circle cx="15" cy="15" r="4" fill="#004b70"/></svg></div></div>
  <h3>BUSINES LOAN</h3>
  <ul><li>Long Term</li><li>Short term</li><li>Equipment and Leasing</li></ul>
  <svg class="go" width="20" height="20" viewBox="0 0 20 20"><circle cx="10" cy="10" r="10" fill="#004b70"/><path d="M8 5l5 5-5 5" stroke="#fff" stroke-width="2.5" fill="none"/></svg>
</article>

<section class="abs about">
  <div class="tab-head"><span>About us</span></div>
  <div class="about-body">
    <p>At Tidewell Lending we work hard to find the right loan for our customers. We do that because we are backed by sound industry knowledge, professional experience and a great customer service approach.</p>
    <p>Tidewell Lending guarantees that we will always tailor the best solution for your individual lending needs.<br>We can do that because we have access to a wide variety of lending options from major banks to non-bank lenders and we are committed to finding the right lending product for you.</p>
    <p>There are many different loan products in the marketplace. Tidewell Lending has access to a wide panel of lenders which means we can access bank and non-bank lenders that meet the individual needs of our customers.</p>
    <p>Contact Tidewell Lending today on: <b>1800 555 210</b> to find out more.</p>
  </div>
</section>

<section class="abs testi">
  <div class="tab-head"><span>Testimonials</span></div>
  <blockquote class="quote">“Lorem ipsum dolor sit amet, consectetur adipisicing elit, sed do eiusmod tempor incididunt ut labore et dolore magna aliqua. Ut enim ad minim veniam.”<cite>Mr. Lorem Ipsum</cite></blockquote>
  <div class="dots"><i class="on"></i><i></i><i></i></div>
</section>

<div class="abs rule"></div>

<section class="abs clients">
  <div class="tab-head"><span>Our clients</span></div>
  <div class="client-row">
    <div>Keystone</div><div>Northcraft</div><div>Meadowly</div><div>Pellar Foods</div><div>Orvell</div>
  </div>
</section>

<footer class="abs footer">
  <div class="fcol" style="left:13px">
    <h4>Contact us</h4>
    <div class="contact-line"><svg width="12" height="12" viewBox="0 0 12 12"><rect width="12" height="12" rx="2" fill="#fff"/><path d="M6 2 2 6h1.5v4h2V8h1v2h2V6H10z" fill="#004b70"/></svg><span>48 Harbour Lane, Marlow Bay<br>2041 Eastvale</span></div>
    <div class="contact-line"><svg width="12" height="12" viewBox="0 0 12 12"><rect width="12" height="12" rx="2" fill="#fff"/><path d="M4 2.5c-1 .5-1.5 1.5-1 3 .7 2 2 3.3 4 4 1.5.5 2.5 0 3-1L8.5 7 7.5 8C6 7.3 4.7 6 4 4.5L5 3.5z" fill="#004b70"/></svg><span>0140 555 382</span></div>
    <div class="contact-line"><svg width="12" height="12" viewBox="0 0 12 12"><rect width="12" height="12" rx="2" fill="#fff"/><rect x="2.5" y="3.5" width="7" height="5" fill="none" stroke="#004b70"/><path d="M2.5 3.5 6 6.5l3.5-3" fill="none" stroke="#004b70"/></svg><span>info@tidewelllending.com</span></div>
  </div>
  <div class="fcol" style="left:257px">
    <h4>Company info</h4>
    <ul><li>Home</li><li>About us</li><li>FAQ</li><li>Contact us</li></ul>
  </div>
  <div class="fcol" style="left:423px">
    <h4>Services</h4>
    <ul><li>Home loans</li><li>Investment loans</li><li>Refinancing loans</li><li>Business loans</li></ul>
  </div>
  <div class="fcol" style="left:614px">
    <h4>Newsletter</h4>
    <div style="color:#d6e3ea">Sign up to our newsletter</div>
    <div class="news-input">Enter your email address</div>
    <div class="news-btn">Sign up</div>
  </div>
  <div class="footer-base">
    <span>Copyright © 2012, tidewelllending.com. All Rights Reserved</span>
    <span>Terms &amp; Condition &nbsp;| &nbsp;Privacy Policy</span>
  </div>
</footer>

</body>
</html>
```